KRV Business Card

Looking for a business card for my restaurant group I own. Four different concepts:

Copperfield Alehouse
Bristow Alehouse
Tanager's Stone Hearth Kitchen
Pellston Patty Company

Card doesn't need to include all the logos.

```html
<!DOCTYPE html>
<html lang="en">
<head>
<meta charset="utf-8">
<title>KRV Business Card</title>
<link href="https://fonts.googleapis.com/css2?family=Poppins:wght@400;500;600&display=swap" rel="stylesheet">
<style>
  :root {
    --stage: #231f20;
    --card-white: #ffffff;
    --gold: #cfae6c;
    --slate: #747579;
    --ink: #4d4d4f;
    --rule: #6d6e71;
  }
  * { margin: 0; padding: 0; box-sizing: border-box; }
  html, body {
    width: 1125px; height: 1200px; overflow: hidden;
    background: var(--stage);
    font-family: "Poppins", sans-serif;
  }
  .card {
    position: absolute; left: 171px; width: 826px; height: 471px; overflow: hidden;
  }
  .card--front { top: 106px; background: var(--card-white); }
  .card--back { top: 639px; background: var(--slate); }

  .brand {
    position: absolute; right: 52px; top: 128px; text-align: right;
    color: var(--gold); font-weight: 500; line-height: 1;
  }
  .brand__name { font-size: 38px; letter-spacing: 4px; }
  .brand__tail { font-size: 19px; letter-spacing: 3px; margin-top: 14px; }

  .person { position: absolute; left: 42px; top: 216px; }
  .person__name { color: var(--gold); font-size: 30px; font-weight: 600; line-height: 1.1; }
  .person__title { color: var(--ink); font-size: 20px; line-height: 1.3; }

  .rule {
    position: absolute; left: 42px; top: 291px; width: 731px; height: 2px; background: var(--rule);
  }

  .contacts { position: absolute; left: 42px; top: 311px; list-style: none; }
  .contacts li {
    display: flex; align-items: center; height: 26px;
    color: var(--ink); font-size: 20px;
  }
  .contacts svg { width: 18px; height: 18px; margin-right: 12px; fill: var(--gold); }

  .address {
    position: absolute; right: 52px; top: 313px; text-align: right;
    color: var(--ink); font-size: 20px; line-height: 25px;
  }

  .edge { position: absolute; left: 0; bottom: 0; width: 826px; height: 60px; }
  .website {
    position: absolute; right: 26px; bottom: 12px;
    color: var(--card-white); font-size: 20px; letter-spacing: 0.8px;
  }

  .monogram {
    position: absolute; right: 70px; top: 340px;
    color: var(--card-white); font-size: 68px; font-weight: 600; letter-spacing: 2px; line-height: 1;
  }
</style>
</head>
<body>
  <section class="card card--front">
    <div class="brand">
      <div class="brand__name">KESTREL RIDGE</div>
      <div class="brand__tail">VENTURES</div>
    </div>

    <div class="person">
      <div class="person__name">Daniel Hartley</div>
      <div class="person__title">President</div>
    </div>

    <div class="rule"></div>

    <ul class="contacts">
      <li><svg viewBox="0 0 24 24"><path d="M6.6 10.8a15 15 0 0 0 6.6 6.6l2.2-2.2a1 1 0 0 1 1-.25 11.4 11.4 0 0 0 3.6.6 1 1 0 0 1 1 1V20a1 1 0 0 1-1 1A17 17 0 0 1 3 4a1 1 0 0 1 1-1h3.5a1 1 0 0 1 1 1c0 1.25.2 2.45.6 3.6a1 1 0 0 1-.25 1z"/></svg>482-617-3049</li>
      <li><svg viewBox="0 0 24 24"><path d="M7 1h10a2 2 0 0 1 2 2v18a2 2 0 0 1-2 2H7a2 2 0 0 1-2-2V3a2 2 0 0 1 2-2zm0 3v15h10V4zm5 16.2a1 1 0 1 0 0 .1z"/></svg>482-730-1926</li>
      <li><svg viewBox="0 0 24 24"><path d="M7 2h8l2 2v6H7zM3 11h18a1 1 0 0 1 1 1v7H2v-7a1 1 0 0 1 1-1zm2 9h14v2H5z"/></svg>482-455-8170</li>
      <li><svg viewBox="0 0 24 24"><path d="M2 6h20v12H2zm1.5 1.2L12 13l8.5-5.8V6.8L12 12 3.5 6.8z"/></svg>name@kestrelridgegroup.com</li>
    </ul>

    <div class="address">
      2914 Wren Hollow Drive<br>
      Fairbanks, Alaska 99709
    </div>

    <svg class="edge" viewBox="0 0 826 60" aria-hidden="true">
      <polygon points="0,40 456,44 450,49 0,49" fill="#6d6e71"/>
      <polygon points="0,52 446,52 442,57 0,57" fill="#cfae6c"/>
      <polygon points="482,13 826,13 826,60 451,60" fill="#cfae6c"/>
    </svg>
    <div class="website">www.kestrelridgegroup.com</div>
  </section>

  <section class="card card--back">
    <div class="monogram">KRV</div>
  </section>
</body>
</html>
```